Insurance Agency website design for Brellow Cover Insurance, LP

Build a website for Brellow Cover Insurance, LP which sells Homeowners, Auto, Renters, Condo, Flood, Disability, Life, Umbrella, and health insurance. We need the coolest insurance agency website out there to get quotes, contact us, or get additional information. Please list the following insurance companies we work with: Varnix, Ostle, Meridale Mutual, Quillor, Dunmarrow, KGZ, and Pellwick.

Make a design similar to https://www.fernagentry.com/

Selling personal insurance policies

```html
<!DOCTYPE html>
<html lang="en">
<head>
<meta charset="utf-8">
<title>Brellow Cover Insurance, LP</title>
<link href="https://fonts.googleapis.com/css2?family=Jost:wght@400;500;600&family=Montserrat:wght@400;500;700&display=swap" rel="stylesheet">
<style>
:root{
  --navy:#0a2a6e;
  --deep:#07276f;
  --blue:#1f6fb8;
  --green:#33cc5e;
  --ink:#1a1a1a;
  --white:#ffffff;
  --soft:#fbfbfd;
}
*{box-sizing:border-box;margin:0;padding:0}
html,body{width:1200px;height:2450px;overflow:hidden}
body{font-family:"Montserrat",sans-serif;color:var(--ink);background:var(--soft);position:relative}
.topbar{height:28px;background:var(--navy);color:var(--white);font:600 10px "Jost",sans-serif;display:flex;justify-content:flex-end;align-items:center;padding-right:140px;gap:10px;letter-spacing:.2px}
.topbar .phone{color:var(--green);font-size:12px;display:flex;align-items:center;gap:6px}
.header{height:90px;background:var(--white);display:flex;align-items:center;justify-content:space-between;padding:0 137px 0 143px}
.brand{display:flex;align-items:center;gap:14px;font:500 23px "Jost",sans-serif;color:var(--navy)}
.brand .mark{width:34px;height:34px;border-radius:50%;background:var(--green)}
.nav{display:flex;align-items:center;gap:35px;font:400 17px "Jost",sans-serif}
.nav a{color:var(--ink);text-decoration:none}
.nav a.active{color:var(--blue)}
.btn{display:inline-block;background:var(--green);color:var(--white);font:400 17px "Jost",sans-serif;padding:4px 16px;border-radius:16px;text-decoration:none}
.nav .btn{margin-left:-25px}
.hero{position:relative;height:544px;background:var(--navy);overflow:hidden}
.hero .photo{position:absolute;left:330px;top:0;right:0;bottom:0;background:linear-gradient(90deg,var(--navy) 0%,#3e62c2 35%,#8aa4e8 70%,#b9c8f2 100%)}
.hero .copy{position:absolute;left:140px;top:72px;width:450px;color:var(--white)}
.hero .rule{width:56px;height:4px;background:var(--green);margin-bottom:24px}
.hero h1{font:500 39px/43px "Jost",sans-serif;text-transform:uppercase;margin-bottom:18px}
.g{color:var(--green)}
.hero p{font-size:13px;line-height:19.5px;margin-bottom:30px}
.partners{height:130px;background:var(--white);border-bottom:1px solid #6f8fbf;display:flex;align-items:center;justify-content:space-between;padding:0 90px 8px}
.partners span{font:500 19px "Jost",sans-serif;color:var(--ink)}
.partners .p1{letter-spacing:5px}
.partners .p2{color:#d6232b;font-weight:600}
.partners .p3{color:#f07a1d}
.partners .p4{color:#20b7bf;font-size:26px}
.partners .p5{color:#1a3f8e}
.partners .p6{letter-spacing:4px;font-size:15px;font-weight:600}
.partners .p7{font-weight:600}
.about{text-align:center;padding-top:74px}
.about h3{font:600 23px "Montserrat",sans-serif;color:var(--navy)}
.about h2{font:500 56px/62px "Jost",sans-serif;color:var(--green);margin-bottom:18px}
.about p{width:890px;margin:0 auto;font-size:13.3px;line-height:24px}
.about .b{color:var(--blue);font-weight:700}
.about .l{color:var(--blue)}
.lines{display:flex;justify-content:center;gap:80px;margin-top:76px}
.line{width:150px;text-align:center}
.line svg{width:110px;height:110px}
.line h4{font:700 19px "Montserrat",sans-serif;color:var(--blue);margin-top:14px}
.dots{display:flex;justify-content:center;gap:9px;margin-top:68px}
.dots i{width:8px;height:8px;border-radius:50%;background:var(--blue)}
.dots i:nth-child(2){background:var(--green)}
.quote{position:relative;height:400px;margin-top:74px}
.quote .copy{position:absolute;left:158px;top:0;width:425px}
.quote h2{font:500 56px/60px "Jost",sans-serif;color:var(--green);margin-bottom:16px}
.quote p{font-size:13.3px;line-height:19.2px;margin-bottom:19px}
.quote .art{position:absolute;left:600px;top:8px;width:485px;height:340px;border-radius:48% 52% 45% 55%;background:radial-gradient(circle at 50% 55%,#dfe9f7,#eef3fb 70%,var(--soft))}
.contact{position:absolute;left:0;top:1880px;width:1200px;height:375px;background:var(--deep);color:var(--white);text-align:center}
.contact .mark{width:58px;height:58px;border-radius:50%;background:var(--green);margin:40px auto 26px}
.contact h2{font:500 49px "Jost",sans-serif;margin-bottom:22px}
.contact p{font:500 40px/46px "Jost",sans-serif}
.footer{position:absolute;left:0;top:2255px;width:1200px;height:195px;background:var(--white)}
.footer .brand{position:absolute;left:146px;top:67px}
.footer .nav{position:absolute;right:140px;top:52px}
.social{position:absolute;right:140px;top:103px;display:flex;gap:14px}
.social i{width:22px;height:22px;border-radius:50%;background:var(--navy)}
.copyr{position:absolute;right:137px;top:146px;font-size:13px;color:var(--navy)}
</style>
</head>
<body>
<div class="topbar">FOR INQUIRIES, PLEASE CONTACT US AT
  <span class="phone"><svg width="11" height="11" viewBox="0 0 24 24"><path fill="#33cc5e" d="M6.6 10.8a15 15 0 0 0 6.6 6.6l2.2-2.2c.3-.3.7-.4 1-.2 1.1.4 2.3.6 3.6.6.6 0 1 .4 1 1V20c0 .6-.4 1-1 1C10.6 21 3 13.4 3 4c0-.6.4-1 1-1h3.5c.6 0 1 .4 1 1 0 1.3.2 2.5.6 3.6.1.3 0 .7-.2 1z"/></svg>(555) 318-2740</span>
</div>
<header class="header">
  <div class="brand"><span class="mark"></span>BRELLOW COVER INSURANCE, LP</div>
  <nav class="nav"><a class="active" href="#">Home</a><a href="#">About</a><a href="#">Services</a><a href="#">Contact Us</a><a class="btn" href="#">Get a Quote</a></nav>
</header>
<section class="hero">
  <div class="photo" role="img" aria-label="Photo of a parent lifting a laughing child in the air outdoors, blue duotone"></div>
  <div class="copy">
    <div class="rule"></div>
    <h1><span class="g">Protect</span> what matters most with <span class="g">Brellow Cover insurance</span></h1>
    <p>At Brellow Cover Insurance, we understand that your peace of mind is invaluable. <b>Our mission</b> is <span class="g">to protect what matters most to you—<b>your home, your vehicle, your health, and your loved ones.</b></span> With our comprehensive range of insurance solutions, we are dedicated to safeguarding your assets and providing you with the security you deserve.</p>
    <a class="btn" href="#">Get a Quote</a>
  </div>
</section>
<div class="partners">
  <span class="p1">VARNIX</span><span class="p2">KGZ</span><span class="p3">Meridale Mutual</span><span class="p4">ostle</span><span class="p5">Quillor</span><span class="p6">PELLWICK</span><span class="p7">DUNMARROW</span>
</div>
<section class="about">
  <h3>ABOUT</h3>
  <h2>BRELLOW COVER INSURANCE</h2>
  <p>Brellow Cover Insurance is a full-service, independent insurance agency with over three decades of experience in delivering comprehensive insurance solutions to individuals. We proudly offer a diverse portfolio of products from more than 20 of the most reputable and financially secure companies in the industry. <span class="b">Our dedicated team of over 50 skilled professionals</span> is committed to customizing these products and services to meet the unique needs of each client. At Brellow Cover Insurance, our experts are focused on addressing the individual needs of our clients, ensuring exceptional <span class="l">service and support at every step.</span></p>
  <div class="lines">
    <div class="line"><svg viewBox="0 0 110 110" fill="none" stroke-width="3"><path d="M12 50 55 12l43 38" stroke="#1f6fb8"/><path d="M22 42v56h66V42" stroke="#1f6fb8"/><rect x="38" y="52" width="34" height="30" stroke="#1f6fb8"/><path d="M55 52v30M38 67h34" stroke="#33cc5e"/></svg><h4>Home Owners</h4></div>
    <div class="line"><svg viewBox="0 0 110 110" fill="none" stroke-width="3"><path d="M6 78V58l12-22h44l10 18" stroke="#1f6fb8"/><path d="M6 78h56" stroke="#1f6fb8"/><circle cx="20" cy="82" r="6" stroke="#1f6fb8"/><path d="M78 40l24 8v22c0 14-12 22-24 28-12-6-24-14-24-28V48z" stroke="#1f6fb8"/><path d="M68 68l8 8 14-16" stroke="#33cc5e"/></svg><h4>Auto</h4></div>
    <div class="line"><svg viewBox="0 0 110 110" fill="none" stroke-width="3"><path d="M10 50 40 24l30 26" stroke="#33cc5e"/><path d="M18 44v30h44V44" stroke="#33cc5e"/><circle cx="26" cy="88" r="10" stroke="#1f6fb8"/><path d="M36 88h60l-6 8M80 88v8" stroke="#1f6fb8"/></svg><h4>Renters</h4></div>
    <div class="line"><svg viewBox="0 0 110 110" fill="none" stroke-width="3"><rect x="36" y="8" width="38" height="94" stroke="#1f6fb8"/><rect x="12" y="40" width="24" height="62" stroke="#1f6fb8"/><rect x="74" y="30" width="24" height="72" stroke="#1f6fb8"/><path d="M46 22h6M58 22h6M46 38h6M58 38h6M46 54h6M58 54h6M46 70h6M58 70h6M20 56h8M20 72h8M82 46h8M82 62h8M82 78h8" stroke="#33cc5e"/><path d="M6 102h98" stroke="#1f6fb8"/></svg><h4>Condo</h4></div>
  </div>
  <div class="dots"><i></i><i></i><i></i></div>
</section>
<section class="quote">
  <div class="copy">
    <h2>GET A QUOTE</h2>
    <p>We believe that securing your home is one of the most important decisions you can make. Obtaining a comprehensive insurance quote is essential to understanding your coverage options and ensuring that your property is adequately protected against unforeseen events.</p>
    <p>Our team of experienced professionals is here to guide you through the process, helping you find the right policy that meets your specific needs and budget. Don’t leave your home’s safety to chance—get a quote today and take the first step towards peace of mind.</p>
    <a class="btn" href="#">Get a Quote</a>
  </div>
  <div class="art" role="img" aria-label="Illustration of a calm person sitting cross-legged surrounded by insurance symbols: house, car, calculator, shield and checklist"></div>
</section>
<section class="contact">
  <div class="mark"></div>
  <h2>FOR INQUIRIES, PLEASE</h2>
  <p>Contact us at <span class="g">(555) 318-2740</span><br>or <span class="g">info@BrellowCover.com.</span></p>
</section>
<footer class="footer">
  <div class="brand"><span class="mark"></span>BRELLOW COVER INSURANCE, LP</div>
  <nav class="nav"><a class="active" href="#">Home</a><a href="#">About</a><a href="#">Services</a><a href="#">Contact Us</a></nav>
  <div class="social"><i></i><i></i><i></i><i></i></div>
  <div class="copyr">© 2025 &nbsp;|&nbsp; www.brellowcover.com</div>
</footer>
</body>
</html>
```